Telecommunications/Power civil contractor needs business card design

Were a new telecommunications/power underground civil contractor that is looking for a new business card design. Our company colours are silver or grey and orange. Feel free to use the white background logo or the black background logo.

Target Market(s)

Local contractors, utility companies, private sector mining/energy companies, developers.

Industry/Entity Type

Telecommunications

Contact Information for Business Card

Each card will need the following info:
Persons name:
Title:
E-mail:
Phone number:
Shop Address:
Mailing Address:

Requirements
Must have
• Each card will need the following info:
• Persons name:
• Title:
• E-mail:
• Phone number:
• Shop Address:
• Mailing Address:

```html
<!DOCTYPE html>
<html lang="en">
<head>
<meta charset="utf-8">
<title>Lark Lane Contracting Inc – Business Card</title>
<link rel="stylesheet" href="https://fonts.googleapis.com/css2?family=Saira:wght@400;600;700&family=Open+Sans:wght@400;600&display=swap">
<style>
  :root {
    --stage: #e6e3df;
    --card: #0b0b0c;
    --orange: #ee6a2e;
    --silver: #a9abae;
    --white: #f4f4f4;
    --muted: #c9c9cb;
  }
  * { box-sizing: border-box; margin: 0; padding: 0; }
  html, body { width: 1200px; height: 1022px; overflow: hidden; }
  body {
    background: var(--stage);
    display: flex; align-items: center; justify-content: center;
    font-family: "Open Sans", Arial, sans-serif;
  }
  .business-card {
    position: relative;
    width: 900px; height: 514px;
    background: var(--card);
    border-radius: 22px;
    overflow: hidden;
    box-shadow: 0 18px 40px rgba(0,0,0,.25);
  }
  .brand-disc {
    position: absolute; left: 70px; top: 150px;
    width: 300px; height: 300px;
    border-radius: 50%;
    border: 14px solid var(--silver);
  }
  .identity {
    position: absolute; left: 430px; top: 48px;
  }
  .company-name {
    font-family: "Saira", Arial, sans-serif;
    font-weight: 700; font-size: 40px; line-height: 1;
    color: var(--white); letter-spacing: 1px; text-transform: uppercase;
  }
  .person-name {
    margin-top: 18px;
    font-family: "Saira", Arial, sans-serif;
    font-weight: 600; font-size: 34px; line-height: 1;
    color: var(--orange); letter-spacing: 1.5px; text-transform: uppercase;
  }
  .person-title {
    margin-top: 8px; font-size: 17px; color: var(--muted);
  }
  .divider {
    position: absolute; left: 380px; right: 40px; top: 232px;
    height: 2px;
    background: linear-gradient(90deg, rgba(169,171,174,0), var(--silver) 20%, var(--silver));
  }
  .details {
    position: absolute; left: 430px; top: 262px;
    display: grid; gap: 20px;
    font-size: 17px; line-height: 1.5; color: var(--white);
  }
  .address-block p { white-space: nowrap; }
  .contact-list { list-style: none; display: grid; gap: 2px; }
  .contact-list li { display: flex; align-items: center; gap: 12px; white-space: nowrap; }
  .contact-icon { width: 16px; height: 16px; flex: none; }
</style>
</head>
<body>
  <main class="business-card">
    <div class="brand-disc" aria-hidden="true"></div>

    <header class="identity">
      <h1 class="company-name">Lark Lane Contracting Inc</h1>
      <h2 class="person-name">Morgan Hale</h2>
      <p class="person-title">Director</p>
    </header>

    <div class="divider"></div>

    <section class="details">
      <div class="address-block">
        <p>PO BOX 4816</p>
        <p>ELM HOLLOW, CA 90210</p>
        <p>48 Quarry Lane</p>
        <p>Brookfield, NY 10580</p>
      </div>

      <ul class="contact-list">
        <li>
          <svg class="contact-icon" viewBox="0 0 16 16" aria-hidden="true"><rect x="4" y="1" width="8" height="14" rx="1.5" fill="none" stroke="#ee6a2e" stroke-width="1.6"/><circle cx="8" cy="12.5" r="0.9" fill="#ee6a2e"/></svg>
          <span>+000 5550-1842</span>
        </li>
        <li>
          <svg class="contact-icon" viewBox="0 0 16 16" aria-hidden="true"><path d="M3 1.5l3 3-1.6 1.6a8 8 0 0 0 5.5 5.5L11.5 10l3 3-2 2C6.5 15 1 9.5 1 3.5z" fill="#ee6a2e"/></svg>
          <span>+000 5550-2391</span>
        </li>
        <li>
          <svg class="contact-icon" viewBox="0 0 16 16" aria-hidden="true"><rect x="1" y="3" width="14" height="10" rx="1" fill="none" stroke="#ee6a2e" stroke-width="1.6"/><path d="M1.5 3.8L8 9l6.5-5.2" fill="none" stroke="#ee6a2e" stroke-width="1.6"/></svg>
          <span>info@larklanecontracting.com</span>
        </li>
        <li>
          <svg class="contact-icon" viewBox="0 0 16 16" aria-hidden="true"><circle cx="8" cy="8" r="6.5" fill="none" stroke="#ee6a2e" stroke-width="1.5"/><ellipse cx="8" cy="8" rx="2.8" ry="6.5" fill="none" stroke="#ee6a2e" stroke-width="1.3"/><path d="M1.5 8h13" stroke="#ee6a2e" stroke-width="1.3"/></svg>
          <span>www.larklanecontracting.com</span>
        </li>
      </ul>
    </section>
  </main>
</body>
</html>
```